Professional Photography Business cards

I need business cards that include my logo which I have uploaded. I run a photography business. I am open to ideas but I would like one side to have my logo and the other side to have my contact info. I don't have a website made but I do own a website domain. I have uploaded 2 different logo color schemes. My business colors are Blue, black , and white.

Business Name
Business Phone Number
Business Email
Business Website address
Instagram

Industry/Entity Type

Professional Photography

Contact Information for Business Card

Phone Number: 916-384-7702 email: info@tlane-studio.example Instagram: @t.lanestudio website doman- www.tlane-studio.example

Requirements
Must have
• I like the idea of a business card with a full black background front and back of card. My colors must include royal blue, black, and white

```html
<!DOCTYPE html>
<html lang="en">
<head>
<meta charset="utf-8">
<title>T. Lane Studio — Business Card</title>
<link rel="stylesheet" href="https://fonts.googleapis.com/css2?family=Roboto:wght@400&display=swap">
<style>
  :root {
    --backdrop: #b8b8b8;
    --card-black: #000000;
    --royal-blue: #0a12a8;
    --panel-blue: #0710a0;
    --panel-light: #3a44d0;
    --icon-blue: #2a34d8;
    --name-blue: #1a24d0;
    --white: #ffffff;
  }
  html, body {
    margin: 0;
    padding: 0;
    width: 1200px;
    height: 801px;
    overflow: hidden;
    background: var(--backdrop);
    font-family: "Roboto", Arial, sans-serif;
  }
  .stage {
    position: relative;
    width: 1200px;
    height: 801px;
  }
  .card {
    position: absolute;
    top: 274px;
    width: 443px;
    height: 263px;
    background: var(--card-black);
    overflow: hidden;
  }
  .card--contact { left: 153px; }
  .card--brand { left: 625px; }

  .brand-panel {
    position: absolute;
    left: 0;
    top: 0;
    width: 190px;
    height: 263px;
    background: radial-gradient(circle at 45% 58%, var(--panel-light) 0%, var(--panel-blue) 55%, var(--royal-blue) 100%);
  }

  .wordmark__name {
    position: absolute;
    color: var(--name-blue);
    font-weight: 400;
    line-height: 1;
    white-space: nowrap;
  }
  .wordmark__tag {
    position: absolute;
    color: var(--white);
    font-weight: 400;
    line-height: 1;
    white-space: nowrap;
  }
  .card--contact .wordmark__name {
    left: 212px;
    top: 40px;
    font-size: 46px;
  }
  .card--contact .wordmark__tag {
    left: 293px;
    top: 101px;
    font-size: 10px;
    letter-spacing: 15px;
  }

  .contact-list {
    position: absolute;
    left: 212px;
    top: 143px;
    margin: 0;
    padding: 0;
    list-style: none;
    color: var(--white);
    font-size: 13px;
  }
  .contact-list li {
    display: flex;
    align-items: center;
    height: 16px;
  }
  .contact-list li.contact--social { margin-bottom: 26px; height: 18px; }
  .contact-list svg {
    width: 11px;
    height: 11px;
    margin-right: 5px;
    flex: none;
  }
  .contact--social .handle-mark {
    width: 10px;
    height: 10px;
    border: 1.5px solid var(--icon-blue);
    border-radius: 3px;
    margin-right: 6px;
  }

  .card--brand .wordmark__name {
    left: 81px;
    top: 90px;
    font-size: 52px;
  }
  .card--brand .wordmark__tag {
    left: 178px;
    top: 177px;
    font-size: 11px;
    letter-spacing: 16px;
  }
  .brand-ring {
    position: absolute;
    left: 275px;
    top: 108px;
    width: 62px;
    height: 62px;
  }
</style>
</head>
<body>
<main class="stage">

  <section class="card card--contact" aria-label="Card front with contact details">
    <div class="brand-panel" role="img" aria-label="Large brand symbol decoration in royal blue and white"></div>

    <span class="wordmark__name">T. Lane</span>
    <span class="wordmark__tag">STUDIO</span>

    <ul class="contact-list">
      <li class="contact--social"><span class="handle-mark" aria-hidden="true"></span>@t.lanestudio</li>
      <li>
        <svg viewBox="0 0 24 24" aria-hidden="true"><path fill="var(--icon-blue)" d="M6.6 10.8a15.1 15.1 0 0 0 6.6 6.6l2.2-2.2a1 1 0 0 1 1-.25 11.4 11.4 0 0 0 3.6.6 1 1 0 0 1 1 1V20a1 1 0 0 1-1 1A17 17 0 0 1 3 4a1 1 0 0 1 1-1h3.5a1 1 0 0 1 1 1c0 1.25.2 2.45.6 3.6a1 1 0 0 1-.25 1z"/></svg>
        916-384-7702
      </li>
      <li>
        <svg viewBox="0 0 24 24" aria-hidden="true"><rect x="2" y="5" width="20" height="14" fill="var(--icon-blue)"/><path d="M2 5l10 8 10-8" stroke="var(--card-black)" stroke-width="1.6" fill="none"/></svg>
        info@tlane-studio.example
      </li>
      <li>
        <svg viewBox="0 0 24 24" aria-hidden="true"><g fill="none" stroke="var(--icon-blue)" stroke-width="2"><circle cx="12" cy="12" r="10"/><ellipse cx="12" cy="12" rx="4.5" ry="10"/><path d="M2 12h20M4 7h16M4 17h16"/></g></svg>
        www.tlane-studio.example
      </li>
    </ul>
  </section>

  <section class="card card--brand" aria-label="Card back with brand name">
    <span class="wordmark__name">T. Lane</span>
    <span class="wordmark__tag">STUDIO</span>
    <svg class="brand-ring" viewBox="0 0 62 62" aria-hidden="true">
      <circle cx="31" cy="31" r="28" fill="none" stroke="var(--white)" stroke-width="4"/>
    </svg>
  </section>

</main>
</body>
</html>
```